Business card for medical clinic

I need an upmarket, modern medical/health business card for my clinic

Contact Information for Business Card

name, address, email, qr code

```html
<!DOCTYPE html>
<html lang="en">
<head>
<meta charset="utf-8">
<title>Cedra Health Clinic – Business Card</title>
<link href="https://fonts.googleapis.com/css2?family=Montserrat:wght@400;500;700;800&display=swap" rel="stylesheet">
<style>
  :root {
    --backdrop: #2b2b2d;
    --card: #ffffff;
    --brand-navy: #1d4e7a;
    --brand-blue: #1e8fcf;
    --sky: #25aee6;
    --tab: #3aa0e0;
    --ink: #2a2a2a;
    --deep: #1b2f55;
  }
  * { margin: 0; padding: 0; box-sizing: border-box; }
  html, body {
    width: 1200px; height: 880px; overflow: hidden;
    background: var(--backdrop);
    font-family: "Montserrat", Arial, sans-serif;
  }
  .card {
    position: absolute; left: 280px;
    width: 640px; height: 366px;
    background: var(--card);
    border-radius: 22px;
    overflow: hidden;
    box-shadow: 0 12px 30px rgba(0,0,0,.45);
  }
  .card--front { top: 50px; }
  .card--back { top: 466px; }

  .wordmark {
    position: absolute; display: flex; align-items: center; gap: 16px;
    color: var(--brand-navy); font-weight: 700; letter-spacing: .06em;
    text-transform: uppercase; white-space: nowrap;
  }
  .wordmark__dot {
    border-radius: 50%; background: var(--brand-blue); flex: none;
  }
  .card--front .wordmark { left: 90px; top: 158px; font-size: 34px; }
  .card--front .wordmark__dot { width: 46px; height: 46px; }
  .card--back .wordmark { left: 34px; top: 44px; font-size: 21px; gap: 10px; }
  .card--back .wordmark__dot { width: 28px; height: 28px; }

  .card__wave { position: absolute; inset: 0; }

  .tab {
    position: absolute; right: 0; top: 20px;
    width: 20px; height: 34px; background: var(--tab);
  }
  .person {
    position: absolute; right: 36px; top: 22px; text-align: right;
    color: var(--ink);
  }
  .person__name {
    color: var(--sky); font-weight: 800; font-size: 24px; letter-spacing: .02em;
  }
  .person__role { font-size: 14px; margin-top: 2px; }
  .person__address { font-size: 14px; line-height: 1.35; margin-top: 12px; }

  .contact {
    position: absolute; right: 28px; top: 214px;
    list-style: none; color: #fff; font-size: 14px; text-align: right;
  }
  .contact li {
    display: flex; justify-content: flex-end; align-items: center;
    gap: 8px; line-height: 1.55;
  }
  .contact svg { width: 13px; height: 13px; flex: none; }
</style>
</head>
<body>

<section class="card card--front" aria-label="Card front">
  <div class="wordmark"><span class="wordmark__dot"></span>Cedra Health Clinic</div>
</section>

<section class="card card--back" aria-label="Card back">
  <svg class="card__wave" viewBox="0 0 640 366" preserveAspectRatio="none" aria-hidden="true">
    <defs>
      <linearGradient id="swoosh" x1="0" x2="1">
        <stop offset="0" stop-color="var(--deep)"/>
        <stop offset="1" stop-color="var(--sky)"/>
      </linearGradient>
    </defs>
    <path d="M640,132 C515,132 430,150 378,210 C325,278 245,314 0,320"
          fill="none" stroke="var(--sky)" stroke-width="6"/>
    <path d="M640,150 C520,150 440,168 390,226 C340,292 260,328 0,338 L0,366 L640,366 Z"
          fill="var(--sky)"/>
    <path d="M0,306 C170,298 270,280 320,242" fill="none" stroke="url(#swoosh)" stroke-width="5"/>
  </svg>

  <div class="wordmark"><span class="wordmark__dot"></span>Cedra Health Clinic</div>

  <span class="tab"></span>
  <div class="person">
    <p class="person__name">DANIEL REEVE</p>
    <p class="person__role">Managing Director</p>
    <p class="person__address">Your address, City<br>State, Zip 1234</p>
  </div>

  <ul class="contact">
    <li>123 456 789
      <svg viewBox="0 0 16 16"><path fill="#fff" d="M3 1l3 3-2 2c1 2 3 4 5 5l2-2 3 3-2 3C6 15 1 10 1 3z"/></svg></li>
    <li>123 456 789
      <svg viewBox="0 0 16 16"><rect x="4" y="1" width="8" height="14" rx="1.5" fill="none" stroke="#fff" stroke-width="1.5"/></svg></li>
    <li>info@yourgmail.com
      <svg viewBox="0 0 16 16"><rect x="1" y="3" width="14" height="10" fill="#fff"/><path d="M1 3l7 6 7-6" fill="none" stroke="#25aee6" stroke-width="1.2"/></svg></li>
    <li>www.yourwebsite.com
      <svg viewBox="0 0 16 16"><circle cx="8" cy="8" r="7" fill="#fff"/><path d="M1 8h14M8 1c-3 4-3 10 0 14M8 1c3 4 3 10 0 14" fill="none" stroke="#25aee6" stroke-width="1"/></svg></li>
  </ul>
</section>

</body>
</html>
```